Letterhead for Conveyancing Company

Use existing logo to create a letterhead for a conveyancing company. Must be able to be used in Microsoft Word. Easy to read and professional.
Contact information to be at the bottom.
Bright Oak Conveyancing Pty Ltd
ACN 621 984 736PO Box 535 Campbelltown SA 5074
Mobile - 0461739286
Web address - www.brightoakconveyancing.com.au

Requirements
Must have
• Logo and contact details.
• Simple and professional.

```html
<!DOCTYPE html>
<html lang="en">
<head>
<meta charset="utf-8">
<title>Bright Oak Conveyancing – Letterhead</title>
<link href="https://fonts.googleapis.com/css2?family=Roboto:wght@400;500;700&display=swap" rel="stylesheet">
<style>
  :root {
    --backdrop: #4d4a49;
    --paper: #fafafa;
    --ink: #5f5f5f;
    --ink-strong: #4a4a4a;
    --brand-grey: #7a7a7a;
    --brand-pink: #e0449a;
  }
  * { box-sizing: border-box; margin: 0; padding: 0; }
  html, body {
    width: 1062px; height: 1200px; overflow: hidden;
    background: var(--backdrop);
    font-family: "Roboto", Arial, sans-serif;
  }
  .letterhead {
    position: absolute; left: 200px; top: 132px;
    width: 662px; height: 936px;
    background: var(--paper);
    color: var(--ink);
  }
  .brand-name {
    position: absolute; left: 42px; top: 46px; width: 160px;
    font-size: 30px; line-height: 32px; font-weight: 700;
    color: var(--brand-grey); letter-spacing: -0.5px;
  }
  .contact {
    position: absolute; left: 390px; top: 55px;
    font-size: 10.5px; line-height: 16.5px;
  }
  .contact .company {
    color: var(--brand-pink); font-size: 14px; font-weight: 500;
    margin-bottom: 8px; line-height: 18px;
  }
  .contact-line { display: flex; align-items: center; gap: 6px; }
  .contact-line svg { width: 9px; height: 9px; fill: var(--brand-pink); flex: none; }
  .contact-line .gap { width: 10px; }
  .contact-line .label { color: var(--brand-pink); }
  .body-text { position: absolute; left: 42px; width: 578px; font-size: 10.5px; line-height: 15px; }
  .date { top: 229px; }
  .recipient { top: 273px; }
  .recipient strong { color: var(--ink-strong); font-weight: 500; }
  .salutation { top: 364px; }
  .message { top: 395px; text-align: justify; font-size: 11px; letter-spacing: -0.15px; }
  .message p { margin-bottom: 15px; }
  .sign-off { position: absolute; left: 42px; top: 740px; font-size: 10.5px; line-height: 15px; }
  .sign-off .name { color: var(--ink-strong); font-weight: 500; }
  .signature-area {
    width: 150px; height: 30px; margin: 10px 0 12px -14px;
    background: linear-gradient(90deg, rgba(40,70,120,0.10), rgba(40,70,120,0.02));
  }
  .footer-band {
    position: absolute; left: 0; bottom: 0; width: 100%; height: 24px;
    background: var(--brand-pink);
  }
</style>
</head>
<body>
<main class="letterhead">
  <div class="brand-name">Bright Oak Conveyancing</div>

  <section class="contact">
    <div class="company">Bright Oak Conveyancing Pty Ltd</div>
    <div class="contact-line">
      <svg viewBox="0 0 10 10"><path d="M1 4.5c0-2 8-2 8 0v1H7V4.2C6 3.7 4 3.7 3 4.2v1.3H1zM2.5 6h5l1 3h-7z"/></svg>
      <span>046 173 9286</span><span class="gap"></span>
      <svg viewBox="0 0 10 10"><path d="M3 0h1.5L4 3h2.2l.5-3h1.5L7.7 3H10v1.5H7.5L7.2 6H10v1.5H7l-.5 2.5H5l.5-2.5H3.3L2.8 10H1.3l.5-2.5H0V6h2l.3-1.5H0V3h2.5zM3.8 4.5 3.5 6h2.2L6 4.5z"/></svg>
      <span><span class="label">ACN</span> 583 217 469</span>
    </div>
    <div class="contact-line">
      <svg viewBox="0 0 10 10"><path d="M5 0a5 5 0 1 0 0 10A5 5 0 0 0 5 0zm0 1c.6.5 1.1 1.6 1.3 3H3.7C3.9 2.6 4.4 1.5 5 1zM1 5.5h1.7c0 1.2.3 2.2.7 3A4 4 0 0 1 1 5.5zm0-1a4 4 0 0 1 2.4-3c-.4.8-.7 1.8-.7 3zm4 4.5c-.6-.5-1.1-1.6-1.3-3.5h2.6C6.1 7.4 5.6 8.5 5 9zm1.6-.5c.4-.8.7-1.8.7-3H9a4 4 0 0 1-2.4 3zm.7-4c0-1.2-.3-2.2-.7-3A4 4 0 0 1 9 4.5z"/></svg>
      <span>www.brightoakconveyancing.com.au</span>
    </div>
    <div class="contact-line">
      <svg viewBox="0 0 10 10"><path d="M5 0a3.5 3.5 0 0 0-3.5 3.5C1.5 6 5 10 5 10s3.5-4 3.5-6.5A3.5 3.5 0 0 0 5 0zm0 5a1.5 1.5 0 1 1 0-3 1.5 1.5 0 0 1 0 3z"/></svg>
      <span>PO Box 871 Marlowdale SA 5096</span>
    </div>
  </section>

  <div class="body-text date">30/20/2016</div>

  <div class="body-text recipient">
    <strong>Mr. XYZ Smith</strong><br>
    123, Street No. 123,<br>
    City Name<br>
    Pincode-123456
  </div>

  <div class="body-text salutation">Dear Sir,</div>

  <div class="body-text message">
    <p>Lorem Ipsum is simply dummy text of the printing and typesetting industry. Lorem Ipsum has been the industry's standard dummy text ever since the 1500s, when an unknown printer took a galley of type and scrambled it to make a type specimen book. It has survived not only five centuries, but also the leap into electronic typesetting, remaining essentially unchanged. It was popularised in the 1960s with the release of Pressglyph sheets containing Lorem Ipsum passages, and more recently with desktop publishing software like Quillmark Layout including versions of Lorem Ipsum.</p>
    <p>Lorem Ipsum is simply dummy text of the printing and typesetting industry. Lorem Ipsum has been the industry's standard dummy text ever since the 1500s, when an unknown printer took a galley of type and scrambled it to make a type specimen book. It has survived not only five centuries, but also the leap into electronic typesetting, remaining essentially unchanged. It was popularised in the 1960s with the release of Pressglyph sheets containing Lorem Ipsum passages, and more recently with desktop publishing software like Quillmark Layout including versions of Lorem Ipsum.</p>
    <p>Lorem Ipsum is simply dummy text of the printing and typesetting industry. Lorem Ipsum has been the industry's standard dummy text ever since the 1500s, when an unknown printer took a galley of type and scrambled it to make a type specimen book.</p>
    <p>Lorem Ipsum is simply dummy text of the printing and typesetting industry. Lorem Ipsum has been the industry's standard dummy text ever since the 1500s, when an unknown printer took a galley of type and scrambled it to make a type specimen book.</p>
  </div>

  <div class="sign-off">
    <div class="name">Your Name</div>
    <div class="signature-area" role="img" aria-label="Handwritten signature"></div>
    <div>CEO &nbsp;|&nbsp; Owner</div>
  </div>

  <div class="footer-band"></div>
</main>
</body>
</html>
```